2 Page Brochure - Commercial Roofing Company

We are looking for a double sided brochure, full color, for our commercial roofing company that tells customers a little bit about the company, what we do, and shows a few pictures.
The brochure would need to have our logo and color scheme that coordinates with that logo.
I have uploaded our logo, some ideas I had, and then the idea list also has our website on there if you'd like to take a look around there for some more ideas.
I have also uploaded some photos we'd like to use.
Page size should be 8.5" x 11".
Target Market(s)
Commercial Property Owners
Other font styles liked:
- Match logo font ideally so it's cohesive, but whatever looks best

```html
<!DOCTYPE html>
<html lang="en">
<head>
<meta charset="utf-8">
<title>Summit Ridge Roofing – Commercial Roofing Brochure</title>
<link href="https://fonts.googleapis.com/css2?family=Inter:wght@400;500;700;800&family=Yellowtail&display=swap" rel="stylesheet">
<style>
:root{
  --backdrop:#e4e9f1;
  --paper:#f6f6f5;
  --ink:#111111;
  --orange:#e8571c;
  --dark:#0d0b0a;
  --brown:#6e2a0e;
  --white:#ffffff;
  --placeholder:#dcd8d2;
  --placeholder-edge:#c9c4bc;
}
*{box-sizing:border-box;margin:0;padding:0}
html,body{width:1200px;height:900px;overflow:hidden}
body{background:var(--backdrop);font-family:"Inter",Arial,sans-serif;color:var(--ink);position:relative}
.page{position:absolute;top:98px;width:498px;height:705px;background:var(--paper);overflow:hidden}
.page--front{left:92px}
.page--back{left:610px}
.abs{position:absolute}
.script{font-family:"Yellowtail","Brush Script MT",cursive;font-weight:400}

/* brand */
.brand{left:28px;top:44px;display:flex;align-items:center;gap:8px}
.brand__mark{width:16px;height:16px;background:var(--orange)}
.brand__name{font-weight:800;font-size:17px;line-height:1.05;color:var(--ink);letter-spacing:.3px}

/* photo placeholders */
.photo{position:absolute}
.photo--worker{left:305px;top:10px;width:193px;height:300px;background:linear-gradient(160deg,#f2a65a 0%,#e07a2c 45%,#6b4a36 100%)}
.frame--worker{left:314px;top:50px;width:153px;height:193px;border:1px solid var(--orange)}
.photo--store{left:243px;top:487px;width:232px;height:119px;background:linear-gradient(180deg,#a9bfd8 0%,#cfd6dc 45%,#5c5552 100%);border:1px solid var(--orange)}
.photo--prop{background:var(--placeholder);border:1px solid var(--placeholder-edge)}
.photo--helmet{left:216px;top:462px;width:82px;height:62px}

/* headline */
.headline{left:29px;font-weight:800;font-size:47px;line-height:1;letter-spacing:-1.5px;color:var(--ink)}
.headline--one{top:132px}
.headline--two{top:175px}
.headline-script{left:30px;top:200px;font-size:84px;line-height:1;color:var(--orange);transform:rotate(-5deg)}

/* certified box */
.certified{left:27px;top:323px;width:187px;height:155px;background:linear-gradient(120deg,var(--dark) 35%,var(--brown) 100%);color:var(--white)}
.certified__title{position:absolute;left:15px;top:16px;font-size:13.5px;font-weight:500;line-height:16px}
.certified__list{position:absolute;top:62px;list-style:none;font-size:13px;line-height:20px}
.certified__list--a{left:14px}
.certified__list--b{left:97px}
.certified__more{position:absolute;left:110px;top:104px;font-size:17px;line-height:16px;color:var(--orange);transform:rotate(-6deg)}

/* checklists */
.ticks li{position:relative;padding-left:16px}
.ticks li::before{content:"";position:absolute;left:3px;top:5px;width:4px;height:8px;border:solid var(--orange);border-width:0 2px 2px 0;transform:rotate(40deg)}

.section-title{font-weight:700;font-size:20px;line-height:1;color:var(--orange)}
.installs-title{left:243px;top:315px}
.installs{top:345px;list-style:none;font-size:14px;line-height:20px;color:var(--ink)}
.installs--a{left:243px}
.installs--b{left:381px}
.installs .multi{line-height:15px;padding-top:2px}
.services-title{left:41px;top:515px}
.services{left:41px;top:544px;list-style:none;font-size:14px;line-height:20px}
.services .two-line{line-height:15px;margin:3px 0 4px}

/* service band */
.service-band{left:214px;top:601px;width:225px;height:59px;background:var(--orange);color:var(--white)}
.service-band__icon{position:absolute;left:14px;top:16px}
.service-band__rule{position:absolute;left:51px;top:14px;width:1px;height:31px;background:var(--white)}
.service-band__text{position:absolute;left:62px;top:13px;font-size:13.5px;font-weight:500;line-height:16px}
.service-area{left:242px;top:664px;font-size:26px;line-height:1;color:var(--ink)}
.arrow{position:absolute}

/* back page */
.photo--roof{left:28px;top:27px;width:442px;height:167px;background:linear-gradient(90deg,#2b2b2b 0%,#4b4f55 45%,#9ea3aa 75%,#c9ccd1 100%)}
.intro{left:49px;top:70px;width:222px;font-size:12.4px;line-height:14.2px;letter-spacing:-.2px;color:var(--white)}
.photo--hardhat{left:334px;top:140px;width:90px;height:66px}
.body-copy{left:28px;width:220px;font-size:12.4px;line-height:14.2px;letter-spacing:-.2px;color:var(--ink)}
.body-copy--climate{top:231px}
.body-copy--certs{top:565px}
.plan-box{left:282px;top:219px;width:188px;height:173px;background:var(--orange);color:var(--white);padding:14px 12px 0 15px;font-size:12.4px;line-height:14.1px;letter-spacing:-.2px}
.photo--storefront{left:28px;top:358px;width:257px;height:157px;background:linear-gradient(180deg,#8fa5c7 0%,#a98a6e 40%,#6a5446 80%,#4a4a4a 100%);border:1px solid var(--orange)}
.photo--drill{left:228px;top:468px;width:70px;height:112px}
.cta{left:307px;top:425px;font-weight:700;font-size:27px;line-height:30px;letter-spacing:-.6px}
.cta__accent{color:var(--orange)}
.contacts{left:305px;top:545px;width:165px;height:160px;background:linear-gradient(180deg,var(--dark) 40%,var(--brown) 100%);color:var(--white)}
.contacts__title{position:absolute;left:0;right:0;top:23px;text-align:center;font-weight:800;font-size:21px;line-height:1}
.contacts__list{position:absolute;left:25px;top:61px;list-style:none;font-size:12.4px;line-height:20px;white-space:nowrap}
.contacts__list li{display:flex;align-items:center;gap:7px}
.contacts__list svg{flex:none}
</style>
</head>
<body>

<section class="page page--front" aria-label="Brochure front page">
  <div class="photo photo--worker" role="img" aria-label="Smiling roofer in hard hat and safety vest with arms crossed, clay roof tiles and a wrench"></div>
  <div class="abs frame--worker"></div>

  <div class="abs brand">
    <span class="brand__mark"></span>
    <span class="brand__name">SUMMIT RIDGE<br>ROOFING</span>
  </div>

  <h1>
    <span class="abs headline headline--one">Quality</span>
    <span class="abs headline headline--two">Commercial</span>
    <span class="abs headline-script script">Roofs</span>
  </h1>

  <div class="abs certified">
    <p class="certified__title">Certified with the<br>Following Manufacturers</p>
    <ul class="certified__list certified__list--a ticks">
      <li>Apexa</li><li>Northline</li><li>Crestmark</li><li>Duraply</li>
    </ul>
    <ul class="certified__list certified__list--b ticks">
      <li>Kovo</li><li>Shieldex</li>
    </ul>
    <p class="certified__more script">And<br>more!</p>
  </div>

  <h2 class="abs section-title installs-title">Installations</h2>
  <ul class="abs installs installs--a ticks">
    <li>TPO</li><li>PVC</li><li>Modified Bitumen</li><li>Silicone Coatings</li><li>Acrylic Coatings</li>
  </ul>
  <ul class="abs installs installs--b ticks">
    <li>Shingle</li><li>Metal</li><li>Tile</li><li class="multi">Spray<br>Polyurethane<br>Foam</li>
  </ul>

  <h2 class="abs section-title services-title">Services</h2>
  <ul class="abs services ticks">
    <li>New Roof Installation</li>
    <li>Re-roofing</li>
    <li class="two-line">Roof Maintenance<br>and Service</li>
    <li>Roof Inspections</li>
    <li>Roof Coatings</li>
  </ul>

  <div class="photo photo--store" role="img" aria-label="Newly roofed commercial storefront with a company work truck in the parking lot"></div>
  <div class="photo photo--prop photo--helmet" role="img" aria-label="Hard hat photo"></div>

  <div class="abs service-band">
    <svg class="service-band__icon" width="26" height="26" viewBox="0 0 26 26" aria-hidden="true">
      <g stroke="#fff" stroke-width="3" stroke-linecap="round" fill="none">
        <line x1="4" y1="22" x2="20" y2="6"/>
        <line x1="6" y1="6" x2="22" y2="22"/>
        <path d="M16 3 l7 7"/>
        <circle cx="5" cy="5" r="3"/>
      </g>
    </svg>
    <span class="service-band__rule"></span>
    <p class="service-band__text">We service the entire<br>state of Arizona.</p>
  </div>
  <p class="abs service-area script">Service Area</p>
  <svg class="arrow" style="left:150px;top:660px" width="46" height="24" viewBox="0 0 46 24" aria-hidden="true">
    <path d="M4 20 Q24 22 40 6" stroke="#111" stroke-width="1.3" fill="none"/>
    <path d="M33 6 L41 5 L39 12" stroke="#111" stroke-width="1.3" fill="none"/>
  </svg>
</section>

<section class="page page--back" aria-label="Brochure back page">
  <div class="photo photo--roof" role="img" aria-label="Aerial view of a white commercial flat roof with rooftop units"></div>
  <p class="abs intro">Summit Ridge Roofing opened the doors in 1984, and we’ve since installed, serviced, maintained, and coated thousands of commercial roofs around the state of Arizona, in the many climate regions of the state.</p>
  <div class="photo photo--prop photo--hardhat" role="img" aria-label="Hard hat photo"></div>

  <p class="abs body-copy body-copy--climate">Though we all live here for the constant sunshine, Arizona is one of the harshest environments in the US for roofs. Constant sun, heat, dryness, and then the torrential monsoon downpours all test the limits of your roof.</p>

  <div class="abs plan-box">We work with you to come up with a solution that works for your roof and will keep your business dry for years to come. Then, our team of project managers, superintendents, foremen, and field workers all come together to execute on that plan and install a quality roof.</div>

  <div class="photo photo--storefront" role="img" aria-label="Brick restaurant building at dusk with completed roof edge"></div>
  <div class="photo photo--prop photo--drill" role="img" aria-label="Cordless drill photo"></div>

  <h2 class="abs cta">Book your<br><span class="cta__accent">Appointment<br>Today!</span></h2>
  <svg class="arrow" style="left:430px;top:496px" width="26" height="38" viewBox="0 0 26 38" aria-hidden="true">
    <path d="M22 2 Q22 24 6 34" stroke="#111" stroke-width="1.3" fill="none"/>
    <path d="M5 26 L5 35 L13 34" stroke="#111" stroke-width="1.3" fill="none"/>
  </svg>

  <p class="abs body-copy body-copy--certs">We are certified with many different manufacturers, so we’re able to offer custom solutions to solve your issues, that will also often come with reputable manufacturer warranties.</p>

  <div class="abs contacts">
    <h2 class="contacts__title">Contacts</h2>
    <ul class="contacts__list">
      <li>
        <svg width="11" height="11" viewBox="0 0 24 24" aria-hidden="true"><path fill="#e8571c" d="M6.6 10.8a15.1 15.1 0 0 0 6.6 6.6l2.2-2.2c.3-.3.7-.4 1-.2 1.1.4 2.3.6 3.6.6.6 0 1 .4 1 1V20c0 .6-.4 1-1 1A17 17 0 0 1 3 4c0-.6.4-1 1-1h3.5c.6 0 1 .4 1 1 0 1.3.2 2.5.6 3.6.1.3 0 .7-.2 1z"/></svg>
        555-014-2200
      </li>
      <li>
        <svg width="11" height="11" viewBox="0 0 24 24" aria-hidden="true"><path fill="#fff" d="M5 2 L19 14 L12.5 14.5 L16 21 L13 22.5 L9.5 16 L5 20 Z"/></svg>
        sr-roofing.com
      </li>
      <li>
        <svg width="12" height="10" viewBox="0 0 24 20" aria-hidden="true"><rect x="1" y="1" width="22" height="18" rx="2" fill="#e8571c"/><rect x="4" y="6" width="6" height="6" fill="#fff"/><rect x="12" y="6" width="8" height="2" fill="#fff"/><rect x="12" y="10" width="8" height="2" fill="#fff"/></svg>
        AZ ROC 100245
      </li>
    </ul>
  </div>
</section>

</body>
</html>
```